Women's Jewellery startup needs a captivating, beautifully designed and intuitive online store

[12/24 update]

Added 2 additional documents:

Feedback on designs received so far: designer feedback.docx
Product images from catalogue: products images.docx

Please read the feedback provided on designs provided so far to guide you further on your submission. The product images can be used to create promotional banners for the site.

@@@Added a document (VELISTO JEWELLERY_checklist.docx) which can be used by designers as a checklist when submitting their designs to ensure all aspects of the requirements have been covered @@@

+++IMPORTANT BUT NOT SPECIFIED IN THE REQUIREMENTS DOCUMENT - DESIGN SHOULD INCLUDE SUPPORT FOR MOBILE FRIENDLY SITE TOO+++

***Previous experience designing Jewellery online stores preferred (not essential)***

The name of the online Jewellery store is "Velisto Jewellery" and the business is based in Hong Kong. It will be run by 2 stay at home mothers. We need a Shopify themed store designed that will achieve the following objectives in order of priority:

• Conversion: The primary objective of the design/content is to prompt the customer to make a purchase. While this may sound obvious, it is mentioned so as not to distract the design process by focusing on other objectives (which are also important). The site also needs to be optimized so as to rank high in search engine searches for relevant keywords (SEO)
• Navigation: An intuitive interface which takes away a lot of the thinking from the customer by making it obvious what they need to do when they visit the store
• Engagement: Encourages the customer to spend time on the website and share content with their social network

Where applicable, the design of the store should reflect as closely as possible the mission statements and words outlined below:

• Jewellery you’ll fall in love with
• We want every client to leave the store with a smile
• We want to be able to provide the best service we can in every situation no matter what
• We aim to increase our business by word of mouth; therefore we tell people things about our store that makes it interesting for them to share
• We love every customer, no matter how difficult things get
• We, as a team, are so well informed about our products and brands that we always have the best information for our customers
• We celebrate women here!
• We celebrate life in here!
• We celebrate beauty here!
• We celebrate families here, as jewellery often stays within families.
• We will always try to make an extra step
• We will always try to exceed the expectation of our customers
• We will go as far as we possibly can to attract a customer back to our store and connect with us
• Every client that leaves our store knows more about jewellery because we passionately told him about it
• Romantic, classic, love, warm, cool, stylish

A draft functional specification is attached with this brief. We would like the design to reflect as closely as possible the functional requirements outlined in the document. Open to suggestions to improve upon the functional requirements.

Target Market(s)

Women aged 18-55

Industry/Entity Type

Jewelry Store

Coding

Coded - Design and coding required

Number of Pages Required

5+ page

Font styles to use
Other font styles liked:
• Myriad Pro as per Logo but open to any font that complements this one

Requirements
Must have
• 1. A look that encourages the user to make a purchase
• 2. An intuitive, easy to navigate and engaging interface
• 3. Primary colour scheme as defined in the functional specification attached
• 4. Simplistic look, not too cluttered
Nice to have
• 1. Closely matching the functional requirements of the site as outlined in the requirements specification but open to any better ideas

```html
<!DOCTYPE html>
<html lang="en">
<head>
<meta charset="utf-8">
<title>Velisto Jewellery</title>
<link href="https://fonts.googleapis.com/css2?family=Cinzel:wght@400;600;700&family=Open+Sans:wght@400;600;700&display=swap" rel="stylesheet">
<style>
:root{
  --gold:#c9a24c;
  --gold-light:#e2c27a;
  --gold-dark:#9a7630;
  --black:#0d0d0d;
  --ink:#1a1a1a;
  --grey:#4a4a4a;
  --muted:#8a8a8a;
  --white:#ffffff;
  --paper:#f6f6f6;
}
*{box-sizing:border-box;margin:0;padding:0}
html,body{width:1200px;height:3008px;overflow:hidden}
body{font-family:"Open Sans",Arial,sans-serif;color:var(--ink);background:var(--white)}
.wrap{width:1080px;margin:0 auto;position:relative}

/* header */
.site-header{background:var(--black);height:166px;color:var(--white)}
.header-inner{height:166px}
.phone{position:absolute;left:0;top:14px;font-size:15px;color:var(--gold-light);display:flex;gap:8px;align-items:center}
.promo-note{position:absolute;left:0;top:50px;display:flex;gap:14px;align-items:center;font-size:12px;line-height:17px;color:#ddd}
.promo-thumb{width:70px;height:60px;background:radial-gradient(circle at 40% 40%,#e8e8e8,#5a5a5a 70%,#1a1a1a);border-radius:4px}
.logo{position:absolute;left:50%;top:26px;transform:translateX(-50%);text-align:center}
.logo-mark{display:flex;align-items:center;gap:10px;justify-content:center}
.logo-square{width:22px;height:22px;background:var(--gold)}
.logo-name{font-family:"Open Sans",Arial,sans-serif;font-weight:600;font-size:30px;letter-spacing:6px;color:var(--gold)}
.logo-tag{font-size:10px;letter-spacing:3px;color:#bbb;margin-top:4px}
.util{position:absolute;right:0;top:12px;display:flex;gap:18px;font-size:12px;color:#ddd}
.cart{position:absolute;right:0;top:50px;font-size:13px;color:var(--gold-light);display:flex;gap:6px;align-items:center}
.search{position:absolute;right:0;top:86px;width:270px;height:32px;background:var(--white);border-radius:2px;font-size:12px;color:var(--muted);padding:8px 12px}
.search svg{position:absolute;right:10px;top:9px}

/* nav */
.main-nav{background:linear-gradient(var(--gold-light),var(--gold));height:30px}
.main-nav ul{list-style:none;display:flex;justify-content:space-between;align-items:center;height:30px;width:1080px;margin:0 auto}
.main-nav li{font-size:11px;font-weight:700;letter-spacing:1px;color:var(--ink)}
.main-nav li.offers{background:var(--gold-dark);color:var(--white);padding:8px 26px}

/* hero */
.hero{height:484px;background:linear-gradient(90deg,#050505 0%,#232323 45%,#0b0b0b 100%);position:relative;overflow:hidden}
.hero-image{position:absolute;left:60px;top:20px;width:560px;height:440px;background:radial-gradient(ellipse at 55% 55%,#d8d8d8 0%,#6f6f6f 35%,#1b1b1b 70%,transparent 80%)}
.hero-copy{position:absolute;left:740px;top:150px;width:370px;text-align:center}
.hero-copy h1{font-family:"Cinzel",Georgia,serif;font-weight:400;font-size:52px;letter-spacing:6px;color:var(--white)}
.hero-copy h2{font-family:"Cinzel",Georgia,serif;font-weight:400;font-size:18px;letter-spacing:4px;color:var(--gold-light);margin-top:2px}
.hero-copy p{font-size:11px;line-height:16px;color:#bbb;margin:12px auto 0;width:280px}
.btn-light{display:inline-block;margin-top:18px;background:var(--white);color:var(--ink);font-size:11px;font-weight:700;letter-spacing:1px;padding:8px 16px}
.dots{position:absolute;bottom:18px;left:50%;transform:translateX(-50%);display:flex;gap:8px}
.dots i{width:9px;height:9px;border-radius:50%;border:1px solid #888;display:block}
.dots i.on{background:var(--gold)}

/* section titles */
.section-title{font-family:"Cinzel",Georgia,serif;font-weight:600;font-size:30px;color:var(--gold);letter-spacing:2px;display:flex;align-items:center;justify-content:center;gap:18px}
.section-title::before,.section-title::after{content:"";width:60px;height:1px;background:var(--gold)}

/* categories */
.categories{height:340px;background:var(--black);text-align:center;padding-top:48px}
.cat-list{display:flex;justify-content:center;gap:88px;margin-top:56px}
.cat{width:110px}
.cat-icon{width:96px;height:96px;border-radius:50%;background:#1d1d1d;border:2px solid #3a3a3a;margin:0 auto;display:flex;align-items:center;justify-content:center}
.cat-label{color:var(--white);font-size:13px;font-weight:600;letter-spacing:1px;margin-top:18px}

/* difference */
.difference{height:580px;background:var(--white);padding-top:46px}
.difference .section-title{font-size:28px}
.intro{width:900px;margin:18px auto 0;text-align:center;font-size:12px;line-height:19px;color:var(--grey)}
.values{display:grid;grid-template-columns:1fr 1fr;column-gap:40px;margin-top:28px}
.values ul{list-style:none}
.values li{font-size:12px;line-height:17px;color:var(--grey);padding:6px 0 6px 24px;position:relative;border-bottom:1px solid #eee}
.values li svg{position:absolute;left:0;top:8px}

/* promo band */
.promo-band{height:360px;background:linear-gradient(180deg,#e0bd6c 0%,#c9a24c 55%,#b48a36 100%);position:relative;overflow:hidden}
.promo-left{position:absolute;left:0;top:0;width:260px;height:360px;background:radial-gradient(circle at 45% 55%,#f3dca6,#c99a55 40%,transparent 70%)}
.promo-right{position:absolute;right:0;top:0;width:280px;height:360px;background:radial-gradient(circle at 55% 55%,#f1e6cf,#c6a160 45%,transparent 72%)}
.promo-copy{position:absolute;left:240px;right:260px;top:96px;text-align:center}
.promo-copy .kicker{font-family:"Cinzel",Georgia,serif;font-size:28px;font-weight:600;color:var(--ink);letter-spacing:2px}
.promo-copy h2{font-family:"Cinzel",Georgia,serif;font-size:46px;font-weight:600;color:var(--ink);letter-spacing:1px;line-height:50px}
.promo-copy p{font-family:"Cinzel",Georgia,serif;font-size:14px;color:var(--white);letter-spacing:1px;margin-top:6px}
.pills{display:flex;justify-content:center;gap:10px;margin-top:20px}
.pills span{background:var(--ink);color:var(--white);font-size:10px;font-weight:700;letter-spacing:1px;padding:6px 12px;border-radius:12px}

/* catalogue */
.catalogue{height:792px;background:var(--white);padding-top:40px}
.row{display:flex;gap:24px;margin-top:30px}
.row + .row{margin-top:24px}
.card{flex:1;border:1px solid #ddd}
.card-head{height:42px;background:#555;color:var(--white);font-size:16px;letter-spacing:1px;text-align:center;line-height:42px;font-family:"Cinzel",Georgia,serif;font-weight:600}
.card-img{background:var(--paper)}
.row-a .card-img{height:246px}
.row-b .card-img{height:286px}
.img-diamond{background:radial-gradient(circle at 35% 50%,#2d5d86 0,#9bb6cc 18%,transparent 26%),radial-gradient(circle at 65% 50%,#2d5d86 0,#9bb6cc 18%,transparent 26%),var(--paper)}
.img-rose{background:radial-gradient(circle at 50% 50%,#e9b9a6 0,#f3d8cc 22%,transparent 34%),var(--paper)}
.img-platinum{background:radial-gradient(circle at 50% 55%,#9a9a9a 0,#d6d6d6 22%,transparent 34%),var(--paper)}
.img-gem{background:radial-gradient(circle at 40% 45%,#e79a1e 0,#f4cc7a 16%,transparent 26%),radial-gradient(circle at 60% 60%,#e79a1e 0,#f4cc7a 14%,transparent 24%),var(--paper)}
.img-gold{background:radial-gradient(circle at 50% 50%,#7b1420 0,#d4a44a 18%,transparent 32%),var(--paper)}

/* footer */
.site-footer{height:256px;background:var(--black);color:#cfcfcf;padding-top:30px}
.foot-cols{display:flex;gap:70px}
.foot-title{color:var(--white);font-size:13px;font-weight:700;letter-spacing:1px;margin-bottom:10px}
.foot-col a{display:block;font-size:12px;line-height:20px;color:#bdbdbd;text-decoration:none}
.newsletter{margin-left:auto;width:390px}
.newsletter p{font-size:12px;line-height:18px;color:#bdbdbd}
.sub-form{display:flex;margin-top:16px}
.sub-form .field{flex:1;height:34px;background:var(--white);font-size:12px;color:var(--muted);padding:9px 12px}
.sub-form .go{background:var(--gold);color:var(--ink);font-size:12px;font-weight:700;padding:0 16px;line-height:34px}
.foot-bottom{position:absolute;left:0;right:0;top:150px;border-top:1px solid #2a2a2a;padding-top:26px;display:flex;justify-content:space-between;align-items:center}
.social{display:flex;gap:12px}
.social i{width:30px;height:30px;border-radius:50%;background:var(--gold);display:block}
.copy{font-size:12px;color:#9a9a9a}
</style>
</head>
<body>

<header class="site-header">
  <div class="wrap header-inner">
    <div class="phone">
      <svg width="14" height="14" viewBox="0 0 24 24"><path d="M6.6 10.8a15.1 15.1 0 0 0 6.6 6.6l2.2-2.2c.3-.3.7-.4 1-.2 1.1.4 2.3.6 3.6.6.6 0 1 .4 1 1V20c0 .6-.4 1-1 1A17 17 0 0 1 3 4c0-.6.4-1 1-1h3.5c.6 0 1 .4 1 1 0 1.3.2 2.5.6 3.6.1.3 0 .7-.2 1z" fill="#e2c27a"/></svg>
      (000) 555 0147
    </div>
    <div class="promo-note">
      <div class="promo-thumb" role="img" aria-label="Sparkling diamond earrings"></div>
      <div>Extra 10% off on orders<br>over $120 till<br>March 31st, 2018</div>
    </div>
    <div class="logo">
      <div class="logo-mark"><span class="logo-square"></span><span class="logo-name">VELISTO</span></div>
      <div class="logo-tag">JEWELLERY FOR ALL OCCASIONS</div>
    </div>
    <div class="util">
      <span>♡ Wishlist</span><span>Sign in</span><span>Currency ▾</span>
    </div>
    <div class="cart">
      <svg width="16" height="16" viewBox="0 0 24 24"><path d="M3 4h3l2.4 10h10l2-7H7" fill="none" stroke="#e2c27a" stroke-width="2"/><circle cx="10" cy="19" r="1.6" fill="#e2c27a"/><circle cx="17" cy="19" r="1.6" fill="#e2c27a"/></svg>
      (0) Items in Cart
    </div>
    <div class="search">Search
      <svg width="14" height="14" viewBox="0 0 24 24"><circle cx="10" cy="10" r="6" fill="none" stroke="#666" stroke-width="2"/><path d="M15 15l5 5" stroke="#666" stroke-width="2"/></svg>
    </div>
  </div>
</header>

<nav class="main-nav">
  <ul>
    <li>ABOUT</li><li>RINGS ▾</li><li>BRACELETS ▾</li><li>NECKLACES ▾</li><li>CHARMS ▾</li><li>EARRINGS ▾</li><li>BY MATERIAL ▾</li><li>CONTACT</li><li class="offers">OFFERS</li>
  </ul>
</nav>

<section class="hero">
  <div class="hero-image" role="img" aria-label="Diamond statement necklace on a black display bust"></div>
  <div class="hero-copy">
    <h1>JEWELLERY</h1>
    <h2>FOR ALL OCCASIONS</h2>
    <p>Pieces you will fall in love with, crafted to be worn every day and kept within families for years.</p>
    <span class="btn-light">SHOP NOW ▸</span>
  </div>
  <div class="dots"><i class="on"></i><i></i><i></i></div>
</section>

<section class="categories">
  <h2 class="section-title">SHOP BY CATEGORY</h2>
  <div class="cat-list">
    <div class="cat"><div class="cat-icon"><svg width="50" height="50" viewBox="0 0 50 50" fill="none" stroke="#ddd" stroke-width="2"><circle cx="16" cy="27" r="9"/><circle cx="34" cy="27" r="9"/></svg></div><div class="cat-label">EARRINGS</div></div>
    <div class="cat"><div class="cat-icon"><svg width="50" height="50" viewBox="0 0 50 50" fill="none" stroke="#ddd" stroke-width="2"><circle cx="19" cy="28" r="10"/><circle cx="31" cy="24" r="10"/></svg></div><div class="cat-label">RINGS</div></div>
    <div class="cat"><div class="cat-icon"><svg width="50" height="50" viewBox="0 0 50 50" fill="none" stroke="#ddd" stroke-width="2"><ellipse cx="25" cy="25" rx="15" ry="12"/><ellipse cx="25" cy="25" rx="11" ry="8"/></svg></div><div class="cat-label">BRACELETS</div></div>
    <div class="cat"><div class="cat-icon"><svg width="50" height="50" viewBox="0 0 50 50" fill="none" stroke="#ddd" stroke-width="2"><path d="M10 12c2 14 8 20 15 20s13-6 15-20"/><circle cx="25" cy="37" r="4"/></svg></div><div class="cat-label">NECKLACES</div></div>
    <div class="cat"><div class="cat-icon"><svg width="50" height="50" viewBox="0 0 50 50" fill="none" stroke="#ddd" stroke-width="2"><circle cx="25" cy="18" r="5"/><circle cx="25" cy="33" r="8"/></svg></div><div class="cat-label">CHARMS</div></div>
  </div>
</section>

<section class="difference">
  <div class="wrap">
    <h2 class="section-title">THE VELISTO DIFFERENCE</h2>
    <p class="intro">Our small team in Hong Kong chooses every piece by hand, because we believe jewellery tells the story of a life. We celebrate women, beauty and family, and we want every client to leave our store with a smile and a little more knowledge about the pieces they love. Ask us anything and we will gladly share it.</p>
    <div class="values">
      <ul>
        <li><svg width="14" height="12" viewBox="0 0 14 12"><path d="M1 6l4 4 8-9" fill="none" stroke="#c9a24c" stroke-width="2"/></svg>Jewellery you'll fall in love with</li>
        <li><svg width="14" height="12" viewBox="0 0 14 12"><path d="M1 6l4 4 8-9" fill="none" stroke="#c9a24c" stroke-width="2"/></svg>We want every client to leave the store with a smile</li>
        <li><svg width="14" height="12" viewBox="0 0 14 12"><path d="M1 6l4 4 8-9" fill="none" stroke="#c9a24c" stroke-width="2"/></svg>We want to provide the best service we can in every situation, no matter what</li>
        <li><svg width="14" height="12" viewBox="0 0 14 12"><path d="M1 6l4 4 8-9" fill="none" stroke="#c9a24c" stroke-width="2"/></svg>We grow by word of mouth, so we tell people things about our store worth sharing</li>
        <li><svg width="14" height="12" viewBox="0 0 14 12"><path d="M1 6l4 4 8-9" fill="none" stroke="#c9a24c" stroke-width="2"/></svg>We love every customer, no matter how difficult things get</li>
        <li><svg width="14" height="12" viewBox="0 0 14 12"><path d="M1 6l4 4 8-9" fill="none" stroke="#c9a24c" stroke-width="2"/></svg>We are so well informed about our products that we always have the best information</li>
        <li><svg width="14" height="12" viewBox="0 0 14 12"><path d="M1 6l4 4 8-9" fill="none" stroke="#c9a24c" stroke-width="2"/></svg>We go as far as we possibly can to bring a customer back to our store</li>
      </ul>
      <ul>
        <li><svg width="14" height="12" viewBox="0 0 14 12"><path d="M1 6l4 4 8-9" fill="none" stroke="#c9a24c" stroke-width="2"/></svg>We celebrate women here!</li>
        <li><svg width="14" height="12" viewBox="0 0 14 12"><path d="M1 6l4 4 8-9" fill="none" stroke="#c9a24c" stroke-width="2"/></svg>We celebrate life in here!</li>
        <li><svg width="14" height="12" viewBox="0 0 14 12"><path d="M1 6l4 4 8-9" fill="none" stroke="#c9a24c" stroke-width="2"/></svg>We celebrate beauty here!</li>
        <li><svg width="14" height="12" viewBox="0 0 14 12"><path d="M1 6l4 4 8-9" fill="none" stroke="#c9a24c" stroke-width="2"/></svg>We celebrate families here, as jewellery often stays within families</li>
        <li><svg width="14" height="12" viewBox="0 0 14 12"><path d="M1 6l4 4 8-9" fill="none" stroke="#c9a24c" stroke-width="2"/></svg>We will always try to make an extra step</li>
        <li><svg width="14" height="12" viewBox="0 0 14 12"><path d="M1 6l4 4 8-9" fill="none" stroke="#c9a24c" stroke-width="2"/></svg>We will always try to exceed the expectation of our customers</li>
        <li><svg width="14" height="12" viewBox="0 0 14 12"><path d="M1 6l4 4 8-9" fill="none" stroke="#c9a24c" stroke-width="2"/></svg>Romantic, classic, love, warm, cool, stylish</li>
      </ul>
    </div>
  </div>
</section>

<section class="promo-band">
  <div class="promo-left" role="img" aria-label="Rose gold rings hanging on a red ribbon"></div>
  <div class="promo-right" role="img" aria-label="Pearl and shell drop earrings"></div>
  <div class="promo-copy">
    <div class="kicker">PROMOTIONAL</div>
    <h2>VARIATIONS OF PASSAGES</h2>
    <p>NEW PIECES ADDED EVERY WEEK, FIND THE ONE MADE FOR YOU</p>
    <div class="pills"><span>EARRINGS</span><span>RINGS</span><span>BRACELETS</span><span>NECKLACES</span><span>CHARMS</span></div>
  </div>
</section>

<section class="catalogue">
  <div class="wrap">
    <h2 class="section-title">PRODUCT CATALOGUE</h2>
    <div class="row row-a">
      <div class="card"><div class="card-head">DIAMOND JEWELLERY</div><div class="card-img img-diamond" role="img" aria-label="Blue topaz and diamond stud earrings"></div></div>
      <div class="card"><div class="card-head">ROSE GOLD JEWELLERY</div><div class="card-img img-rose" role="img" aria-label="Rose gold engagement ring with halo setting"></div></div>
    </div>
    <div class="row row-b">
      <div class="card"><div class="card-head">PLATINUM JEWELLERY</div><div class="card-img img-platinum" role="img" aria-label="Platinum solitaire ring"></div></div>
      <div class="card"><div class="card-head">GEMSTONE JEWELLERY</div><div class="card-img img-gem" role="img" aria-label="Citrine gemstone drop earrings"></div></div>
      <div class="card"><div class="card-head">GOLD PLATED JEWELLERY</div><div class="card-img img-gold" role="img" aria-label="Gold plated ring with garnet stone"></div></div>
    </div>
  </div>
</section>

<footer class="site-footer">
  <div class="wrap">
    <div class="foot-cols">
      <div class="foot-col"><h4 class="foot-title">ABOUT US</h4><a>Our Story</a><a>Wholesale Inquiries</a></div>
      <div class="foot-col"><h4 class="foot-title">SHOPPING</h4><a>Orders</a><a>Wishlist</a><a>Size Guide</a></div>
      <div class="foot-col"><h4 class="foot-title">CUSTOMER CARE</h4><a>Returns</a><a>FAQs</a><a>Care &amp; Warranty</a><a>Contact Us</a></div>
      <div class="newsletter">
        <h4 class="foot-title">NEWSLETTER SIGNUP</h4>
        <p>Join our list for new arrivals, care tips and members-only offers.</p>
        <div class="sub-form"><div class="field">Enter Your Email</div><div class="go">SUBSCRIBE</div></div>
      </div>
    </div>
    <div class="foot-bottom">
      <div class="social"><i></i><i></i><i></i></div>
      <div class="copy">© All Rights Reserved</div>
    </div>
  </div>
</footer>

</body>
</html>
```